Digital Transformation Company Trade Show Banners

I am looking for help designing banners for an upcoming trade show. One would be for our company and one would be for our product. I am planning on purchasing retractable banners with a size of 33" x 81". Details are attached.

```html
<!DOCTYPE html>
<html lang="en">
<head>
<meta charset="utf-8">
<title>Vantrel Technology – Retractable Banner</title>
<link href="https://fonts.googleapis.com/css2?family=Montserrat:wght@500;600;700;800&display=swap" rel="stylesheet">
<style>
  :root {
    --white: #ffffff;
    --navy: #1b2a44;
    --deep: #14161f;
    --steel: #2d4f78;
    --orange: #ec7a2c;
    --sky: #2e9be6;
    --ink: #1c1f2a;
  }
  * { margin: 0; padding: 0; box-sizing: border-box; }
  html, body { width: 1200px; height: 3057px; overflow: hidden; background: var(--white); }
  body { font-family: 'Montserrat', Arial, sans-serif; }
  .banner { position: relative; width: 1200px; height: 3057px; background: var(--deep); overflow: hidden; }

  .brand-bar { position: absolute; left: 0; top: 0; width: 1200px; height: 286px; background: var(--white);
    display: flex; align-items: center; justify-content: center; gap: 26px; }
  .brand-mark { width: 46px; height: 46px; background: var(--orange); }
  .brand-name { font-weight: 700; font-size: 78px; color: var(--navy); letter-spacing: 4px; }

  .hero-visual { position: absolute; left: 0; top: 286px; width: 1200px; height: 1200px;
    background: radial-gradient(ellipse 55% 40% at 50% 18%, #3b6a9c 0%, rgba(45,79,120,0.6) 45%, rgba(20,22,31,0) 100%),
                linear-gradient(180deg, #23476e 0%, #1d3453 40%, var(--deep) 100%); }

  .headline { position: absolute; left: 78px; top: 480px; color: var(--white); font-weight: 600; line-height: 1; }
  .headline .line { display: block; white-space: nowrap; }
  .headline .l1 { font-size: 154px; letter-spacing: 1px; }
  .headline .l2 { font-size: 110px; margin-top: 34px; }
  .headline .thrive { color: var(--orange); font-size: 158px; font-weight: 700; margin-right: 24px; }
  .headline .l3 { font-size: 150px; margin-top: 30px; }
  .headline-rule { position: absolute; left: 100px; top: 1128px; width: 320px; height: 9px; background: var(--orange); }

  .offer { position: absolute; left: 72px; top: 1430px; color: var(--white); }
  .offer-lead { font-weight: 700; font-size: 78px; white-space: nowrap; }
  .offer-lead small { font-size: 46px; font-weight: 700; margin-left: 36px; }
  .offer-title { color: var(--sky); font-weight: 600; font-size: 78px; margin-top: 4px; }

  .services { position: absolute; left: 72px; top: 1700px; list-style: none; }
  .service { position: absolute; left: 0; display: flex; align-items: center; width: 1050px; }
  .service svg { width: 130px; height: 130px; flex: none; }
  .service-name { margin-left: 104px; color: var(--white); font-weight: 600; font-size: 50px; line-height: 1.15; text-transform: uppercase; }

  .contact-bar { position: absolute; left: 0; top: 2807px; width: 1200px; height: 250px; background: var(--orange); color: var(--white); }
  .ask { position: absolute; left: 72px; top: 60px; font-weight: 700; font-size: 56px; line-height: 1.2; }
  .ask .q { color: var(--ink); display: block; }
  .contact-curve { position: absolute; left: 360px; top: 20px; }
  .phone-row, .web-row { position: absolute; left: 480px; display: flex; align-items: center; gap: 30px; }
  .phone-row { top: 52px; }
  .web-row { top: 150px; }
  .phone-number { font-weight: 700; font-size: 74px; }
  .web-address { font-weight: 600; font-size: 52px; }
</style>
</head>
<body>
<main class="banner">
  <header class="brand-bar">
    <span class="brand-mark"></span>
    <span class="brand-name">VANTREL TECHNOLOGY</span>
  </header>

  <div class="hero-visual" role="img" aria-label="Dark blue photo of a hand reaching toward glowing digital technology interface"></div>

  <h1 class="headline">
    <span class="line l1">LOOKING TO</span>
    <span class="line l2"><span class="thrive">THRIVE</span>IN THE</span>
    <span class="line l3">DIGITAL AGE?</span>
  </h1>
  <div class="headline-rule"></div>

  <section class="offer">
    <p class="offer-lead">WE OFFER<small>A WIDE VARIETY OF</small></p>
    <h2 class="offer-title">DIGITAL SERVICES</h2>
  </section>

  <ul class="services">
    <li class="service" style="top:0">
      <svg viewBox="0 0 64 64" fill="none" stroke="#ec7a2c" stroke-width="2.4" stroke-linecap="round" stroke-linejoin="round">
        <circle cx="30" cy="30" r="7"/><circle cx="30" cy="30" r="2.5"/>
        <path d="M30 19v-3M30 44v-3M19 30h-3M44 30h-3M22 22l-2-2M38 38l2 2M38 22l2-2M22 38l-2 2"/>
        <path d="M14 20a20 20 0 0 1 18-12M46 40a20 20 0 0 1-18 12"/><path d="M28 5l4 3-3 4M32 55l-4-3 3-4"/>
        <rect x="44" y="6" width="14" height="18" rx="2"/><path d="M47 12h8M47 16h8"/>
        <rect x="6" y="44" width="16" height="14" rx="2"/><path d="M9 49h10M9 53h10"/>
      </svg>
      <span class="service-name">Digital<br>Transformation</span>
    </li>
    <li class="service" style="top:230px">
      <svg viewBox="0 0 64 64" fill="none" stroke="#ec7a2c" stroke-width="2.4" stroke-linecap="round" stroke-linejoin="round">
        <circle cx="32" cy="32" r="16"/><rect x="25" y="31" width="14" height="11" rx="2"/><path d="M28 31v-4a4 4 0 0 1 8 0v4"/>
        <path d="M32 16V6M20 20l-6-6M44 20l6-6M16 32H6M48 32h10M20 44l-6 6M44 44l6 6M32 48v10"/>
        <circle cx="32" cy="5" r="2"/><circle cx="5" cy="32" r="2"/><circle cx="59" cy="32" r="2"/><circle cx="32" cy="59" r="2"/>
      </svg>
      <span class="service-name">Cybersecurity</span>
    </li>
    <li class="service" style="top:450px">
      <svg viewBox="0 0 64 64" fill="none" stroke="#ec7a2c" stroke-width="2.4" stroke-linecap="round" stroke-linejoin="round">
        <rect x="6" y="10" width="52" height="36" rx="3"/><path d="M24 46v8M40 46v8M18 56h28"/>
        <circle cx="32" cy="28" r="6"/><path d="M32 18v4M32 34v4M22 28h4M38 28h4"/>
        <path d="M12 18h6M12 38h6M46 18h6M46 38h6"/>
      </svg>
      <span class="service-name">Software<br>Development</span>
    </li>
    <li class="service" style="top:680px">
      <svg viewBox="0 0 64 64" fill="none" stroke="#ec7a2c" stroke-width="2.4" stroke-linecap="round" stroke-linejoin="round">
        <path d="M24 40c-4-3-7-8-7-13a15 15 0 0 1 30 0c0 5-3 10-7 13v6H24z"/><path d="M26 50h12M28 55h8"/>
        <path d="M28 30l4 4 4-4M32 34v6"/>
        <path d="M32 4v5M12 10l4 4M52 10l-4 4M5 27h5M54 27h5M8 44l5-3M56 44l-5-3"/>
      </svg>
      <span class="service-name">Technology<br>&nbsp;Solution</span>
    </li>
    <li class="service" style="top:885px">
      <svg viewBox="0 0 64 64" fill="none" stroke="#ec7a2c" stroke-width="2.4" stroke-linecap="round" stroke-linejoin="round">
        <rect x="8" y="6" width="48" height="28" rx="2"/><path d="M14 26l8-8 6 5 10-10 8 6"/>
        <circle cx="18" cy="42" r="4"/><circle cx="32" cy="42" r="4"/><circle cx="46" cy="42" r="4"/>
        <path d="M11 58v-5a7 7 0 0 1 14 0v5M25 58v-5a7 7 0 0 1 14 0v5M39 58v-5a7 7 0 0 1 14 0v5"/>
      </svg>
      <span class="service-name">Training &amp; Workshops</span>
    </li>
  </ul>

  <footer class="contact-bar">
    <p class="ask">HAVE ANY<span class="q">QUESTIONS?</span></p>
    <svg class="contact-curve" width="180" height="50" viewBox="0 0 180 50" fill="none" stroke="#ffffff" stroke-width="3" stroke-linecap="round">
      <path d="M6 40C50 2 120 0 168 32"/><path d="M152 30l16 2-4-15"/>
    </svg>
    <div class="phone-row">
      <svg width="54" height="54" viewBox="0 0 24 24" fill="none" stroke="#ffffff" stroke-width="1.6" stroke-linejoin="round">
        <path d="M5 3h4l2 5-2.5 1.5a11 11 0 0 0 6 6L16 13l5 2v4a2 2 0 0 1-2 2A17 17 0 0 1 3 5a2 2 0 0 1 2-2z"/>
      </svg>
      <span class="phone-number">(855) 555-0142</span>
    </div>
    <div class="web-row">
      <svg width="48" height="48" viewBox="0 0 24 24" fill="none" stroke="#ffffff" stroke-width="1.6">
        <circle cx="12" cy="12" r="10"/><ellipse cx="12" cy="12" rx="4" ry="10"/><path d="M2 12h20M4 6.5h16M4 17.5h16"/>
      </svg>
      <span class="web-address">www.vantrel.io</span>
    </div>
  </footer>
</main>
</body>
</html>
```